NZ First of it's kind solutions directory and marketplace for busy Mums needs a business card design

We need a business card design for our new nationwide business in NZ (long term plans to go global). We provide solutions to the everyday challenges that busy Mums face by connecting them with quality communities and suppliers of carefully selected, relevant products and services. We sell direct via our online marketplace. The final design should communicate our values of inclusivity, quality and smart solutions. Colours should incorporate our logo colour palette of #477077 and #6ba8b2. Our website is at https://www.brightnestmums.example

Target Market(s)

busy Mums, Age 28 – 50, female, income over $100K, location main centres NZ primarily but NZ wide. Is likely juggling work or career with a young family. Probably had hobbies which have fallen by the wayside.
-Wants to succeed in her chosen career without compromising on family life
-to successfully juggle her career without feeling like she is compromising her children
- Is time poor, something always has to give and it’s generally her health (she’ll stay up late, get stressed)
- probably ex corporate or professional career. Has discretional income

Industry/Entity Type

Business

Contact Information for Business Card

Lena Forbisher, Founder, BrightNestMums.example (Strapline Tap; Gather; Sorted), 47 Kowhai Terrace, Ellerslie, Auckland 1051, New Zealand. Mob: 021 483 517 Ph: +64 (0)9 571 4860

Font styles to use
Other font styles liked:
• Raleway, and/or Architects Daughter

Colors
00a990
33b8a4
86cfc6
cfeae6

Requirements
Must have
• the above details, streamline. the logo and colours associated with those logos
Should not have
• foil or metallic colours

```html
<!DOCTYPE html>
<html lang="en">
<head>
<meta charset="utf-8">
<title>BrightNestMums – Business Card</title>
<link href="https://fonts.googleapis.com/css2?family=Roboto:wght@400;500&family=Roboto+Condensed:wght@500&display=swap" rel="stylesheet">
<style>
  :root {
    --backdrop: #1f1f1f;
    --brand-dark: #477077;
    --brand-light: #6ba8b2;
    --card-paper: #f1f1f1;
    --white: #ffffff;
  }
  * { margin: 0; padding: 0; box-sizing: border-box; }
  html, body {
    width: 1200px; height: 960px; overflow: hidden;
    background: var(--backdrop);
    font-family: "Roboto", Arial, sans-serif;
  }
  .canvas { position: relative; width: 1200px; height: 960px; }

  .card { position: absolute; width: 600px; height: 343px; overflow: hidden; }
  .card--front { left: 314px; top: 113px; background: var(--card-paper); }
  .card--back { left: 311px; top: 472px; background: var(--brand-dark); }

  .wave { position: absolute; inset: 0; }

  .contact { position: absolute; left: 30px; top: 24px; color: var(--white); }
  .contact__name {
    font-family: "Roboto Condensed", "Arial Narrow", sans-serif;
    font-weight: 500; font-size: 21px; color: var(--brand-light);
    letter-spacing: 0.2px; line-height: 26px;
  }
  .contact__role { font-size: 15px; line-height: 20px; margin-bottom: 8px; }
  .contact__address { font-size: 14px; line-height: 18px; margin-bottom: 8px; }
  .contact__line { display: flex; align-items: center; font-size: 14px; line-height: 19.5px; }
  .contact__icon { width: 12px; height: 13px; margin-right: 10px; fill: var(--brand-light); }

  .brand {
    position: absolute; right: 46px; top: 272px;
    display: flex; align-items: center; gap: 10px;
  }
  .brand__dot { width: 26px; height: 26px; border-radius: 50%; background: var(--brand-dark); }
  .brand__name { font-size: 28px; font-weight: 500; color: var(--brand-dark); letter-spacing: -0.3px; }

  .back-brand {
    position: absolute; left: 0; right: 0; top: 140px;
    text-align: center; color: var(--white); font-size: 34px; font-weight: 500;
  }
  .strapline {
    position: absolute; left: 0; right: 0; top: 286px;
    text-align: center; color: var(--white); font-size: 14px;
  }
</style>
</head>
<body>
<div class="canvas">

  <section class="card card--front">
    <svg class="wave" viewBox="0 0 600 343" width="600" height="343" aria-hidden="true">
      <path fill="#ffffff" d="M0,195 C30,212 60,228 100,235 C180,250 250,210 330,140 C420,60 480,20 600,30 L600,46 C510,38 450,70 380,135 C300,210 230,262 160,262 C100,262 50,240 0,222 Z"/>
      <path fill="none" stroke="#6ba8b2" stroke-width="6" d="M150,261 C240,258 300,205 380,135 C455,68 515,38 600,45"/>
      <path fill="none" stroke="#477077" stroke-width="4" d="M175,250 C250,240 300,195 370,130 C440,66 500,30 600,34"/>
      <path fill="#477077" d="M0,0 H600 V30 C480,20 420,60 330,140 C250,210 180,250 100,235 C60,228 30,212 0,195 Z"/>
    </svg>

    <div class="contact">
      <div class="contact__name">LENA FORBISHER</div>
      <div class="contact__role">FOUNDER</div>
      <div class="contact__address">47 Kowhai Terrace, Ellerslie<br>Auckland 1051, New Zealand.</div>
      <div class="contact__line">
        <svg class="contact__icon" viewBox="0 0 12 13" aria-hidden="true"><path d="M2,1 L4.5,0.5 L5.5,3.5 L4,4.8 C4.8,6.6 6,7.9 7.6,8.8 L9,7.4 L12,8.6 L11.5,11.2 C6,11.6 1,6.5 2,1 Z"/></svg>
        +64 (0)9 571 4860
      </div>
      <div class="contact__line">
        <svg class="contact__icon" viewBox="0 0 12 13" aria-hidden="true"><path d="M2.5,0 H9.5 V13 H2.5 Z M3.7,1.5 V10 H8.3 V1.5 Z M5.3,11 H6.7 V12 H5.3 Z"/></svg>
        021 483 517
      </div>
      <div class="contact__line">
        <svg class="contact__icon" viewBox="0 0 12 13" aria-hidden="true"><circle cx="6" cy="6.5" r="5.8"/><path fill="#477077" d="M3,3.5 C4.5,3 5.5,4.5 4.8,6 C4.2,7 5.5,8.5 4.5,10 L3.5,9 C2.5,7.5 2.5,5 3,3.5 Z M7.5,2 C9,2.5 10,4 9.5,5 L8,5 Z"/></svg>
        BrightNestMums.example
      </div>
    </div>

    <div class="brand">
      <span class="brand__dot"></span>
      <span class="brand__name">BrightNestMums</span>
    </div>
  </section>

  <section class="card card--back">
    <div class="back-brand">BrightNestMums</div>
    <div class="strapline">Tap; Gather; Sorted</div>
  </section>

</div>
</body>
</html>
```